DeskHarbor - Coworking website design

DeskHarbor is a new global coworking brand, growing fast and establishing stylish locations and communities that inspire innovation and collaboration all around the world.
The project includes a complete website design, focused on delivering the company’s values and messages, provide information to site visitors and to generate leads.

Please review the attached design brief, for more information.

Target Market(s)

Both men and women. Decision makers in:
Small & medium businesses in various fields, but mainly technology firms (Startups or established brands).
Global enterprises.
Dynamic “new generation” companies.
Press

Number of Pages Required

2 page

Requirements
Must have
• Project Scope & deliverables:
• Concept and design for :
• Home page
• Deliver the values mentioned above.
• Showcase the cities in which the company has locations in.
• Show customer testimonials.
• Provide an interface (form) for booking a tour and/or leaving contact details for more information (two alternatives)
• Coworking location page - Each location is in the coolest part of a different major city, and has its own address, set of amenities (kitchen, fast internet etc,), area information (public transportation accessibility, sites near by, bars and restaurants in walking distance) and pricing for private offices (based on number of people per office). Each location page must have an interface to book a location tour.
• Site Navigation (header & footer) - allow simple navigation between multiple city pages, location pages and homepage. Growth of up to 50 locations in 25 cities.
• The navigation should account for Navigation to additional pages (not commissioned in this project) such as:
• Locations
• Enterprise
• Special promotions
• Blog
• Contact us
• About us
• Note - the site should account for geolocation variable display, showing different content for different locations.
• Deliverables must include all editable graphic files (photoshop or similar), as follows:
• Home page - Desktop view (preferably both)
• Location page - Mobile web view (preferably both)
• Navigation - both options

```html
<!DOCTYPE html>
<html lang="en">
<head>
<meta charset="utf-8">
<title>DeskHarbor – Coworking</title>
<link href="https://fonts.googleapis.com/css2?family=Open+Sans:wght@400;600;700&display=swap" rel="stylesheet">
<style>
:root{
  --accent:#8cc7ea;
  --accent-dark:#5fb0e0;
  --ink:#1d1d1d;
  --muted:#666;
  --grey-band:#e6e6e6;
  --footer:#000;
  --white:#fff;
}
*{box-sizing:border-box;margin:0;padding:0}
html,body{width:1200px;height:3422px;overflow:hidden}
body{font-family:"Open Sans",Arial,sans-serif;color:var(--ink);background:var(--white);position:relative}
.abs{position:absolute}

/* hero */
.hero{left:0;top:0;width:1200px;height:560px;background:linear-gradient(180deg,#6f6f6f 0%,#9a9a9a 45%,#bdbdbd 70%,#d8d8d8 100%)}
.hero-photo{position:absolute;inset:0;background:linear-gradient(100deg,#8e8e8e 0%,#b9b9b9 30%,#9c8a7c 55%,#7b6a5d 75%,#9b9b9b 100%);opacity:.9}
.hero-wave{position:absolute;left:0;bottom:0;width:1200px;height:40px}
.logo{font-weight:700;color:var(--white);font-size:32px;letter-spacing:-.5px}
.topbar{right:98px;top:8px;color:var(--white);font-size:15px;display:flex;gap:48px;align-items:center}
.topbar span{display:flex;align-items:center;gap:8px}
.nav{right:98px;top:40px;display:flex;gap:40px;color:var(--white);font-size:15px;font-weight:600}
.hero-title{left:0;width:1200px;top:200px;text-align:center;color:var(--white);font-size:62px;font-weight:700;letter-spacing:1px}
.hero-sub{left:300px;width:600px;top:282px;text-align:center;color:var(--white);font-size:16px;line-height:27px;font-weight:600}

/* sections */
.section-title{left:0;width:1200px;text-align:center;font-size:31px;font-weight:700;color:var(--ink)}
.value{display:flex;gap:38px;width:420px}
.value-icon{width:90px;height:90px;border:2px solid #cfcfcf;border-radius:50%;flex:none;display:flex;align-items:center;justify-content:center}
.value h3{font-size:18px;font-weight:600;margin:0 0 10px}
.value p{font-size:12px;line-height:17px;color:var(--muted);width:240px}
.btn{background:var(--accent);color:var(--white);font-weight:700;font-size:14px;text-align:center;letter-spacing:.5px}

.what{left:0;top:1074px;width:600px;height:361px;background:var(--grey-band)}
.what-photo{left:600px;top:1074px;width:600px;height:361px;background:linear-gradient(180deg,#e8e8e8 0%,#d5d2cc 55%,#a98b6c 75%,#8a6c50 100%)}
.what h2{position:absolute;left:98px;top:44px;font-size:29px;font-weight:700}
.what p{position:absolute;left:98px;width:380px;font-size:13px;line-height:21px;color:#333}

.avatar{width:152px;height:152px;border-radius:50%;background:linear-gradient(160deg,#d9d9d9,#9e9e9e)}
.quote-badge{width:42px;height:42px;border-radius:50%;background:var(--accent);border:3px solid var(--white);color:var(--white);font-weight:700;font-size:22px;display:flex;align-items:center;justify-content:center}
.testimonial-text{width:280px;text-align:center;font-size:14px;line-height:24px;color:#444}

.map{left:0;top:1896px;width:1200px;height:456px;background:linear-gradient(180deg,#86c6ea,#7cbfe6)}
.map-card{left:452px;top:2060px;width:321px;height:116px;background:var(--white);text-align:center}
.map-card h3{font-size:28px;font-weight:400;margin-top:24px;letter-spacing:.5px}
.map-card p{font-size:11px;color:#555;margin-top:4px}

.news-card{top:2484px;width:278px;height:386px;background:var(--white);box-shadow:3px 4px 8px rgba(0,0,0,.18)}
.news-img{width:278px;height:182px}
.news-card p{margin:40px 26px 0;text-align:center;font-size:14px;line-height:23px;color:#333}
.news-meta{position:absolute;left:0;width:278px;bottom:60px;display:flex;justify-content:center;gap:16px;font-size:11px;color:#555}

/* footer */
.footer{left:0;top:2950px;width:1200px;height:472px;background:var(--footer);color:var(--white)}
.footer-wave{position:absolute;left:0;top:-8px;width:1200px;height:36px}
.footer h4{font-size:19px;font-weight:400;letter-spacing:.5px}
.footer .blurb{position:absolute;left:98px;top:130px;width:360px;font-size:13px;line-height:25px}
.quicklinks{position:absolute;left:525px;top:132px;list-style:none;font-size:13px;line-height:25px}
.quicklinks li::before{content:"";display:inline-block;width:5px;height:5px;background:var(--white);border-radius:50%;margin:0 18px 2px 0}
.field{position:absolute;left:760px;width:341px;height:28px;border:1px solid #bfbfbf;font-size:12px;padding:5px 10px}
.socials{position:absolute;left:98px;top:280px;display:flex;gap:28px}
.socials span{width:26px;height:26px;border-radius:50%;border:2px solid var(--white)}
.footer-bottom{position:absolute;left:98px;right:98px;top:408px;border-top:1px solid #555;padding-top:24px;display:flex;font-size:12px}
.footer-bottom ul{margin-left:auto;display:flex;gap:40px;list-style:none}
.footer-bottom li::before{content:"";display:inline-block;width:5px;height:5px;background:var(--white);border-radius:50%;margin:0 14px 2px 0}
</style>
</head>
<body>

<!-- HERO -->
<header class="hero abs">
  <div class="hero-photo" role="img" aria-label="Bright coworking lounge with red armchairs and a wooden table"></div>
  <div class="logo abs" style="left:98px;top:14px">DeskHarbor</div>
  <div class="topbar abs">
    <span><svg width="14" height="14" viewBox="0 0 24 24"><path fill="#8cc7ea" d="M6.6 10.8a15 15 0 0 0 6.6 6.6l2.2-2.2c.3-.3.7-.4 1-.2 1.1.4 2.3.6 3.6.6.6 0 1 .4 1 1V20c0 .6-.4 1-1 1A17 17 0 0 1 3 4c0-.6.4-1 1-1h3.5c.6 0 1 .4 1 1 0 1.3.2 2.5.6 3.6.1.3 0 .7-.2 1z"/></svg>+1 555 010 200</span>
    <span><svg width="16" height="12" viewBox="0 0 16 12"><rect x="1" y="1" width="14" height="10" fill="none" stroke="#8cc7ea" stroke-width="1.5"/><path d="M1 1l7 6 7-6" fill="none" stroke="#8cc7ea" stroke-width="1.5"/></svg>info@deskharbor-mail.com</span>
  </div>
  <nav class="nav abs">
    <span>Home</span><span>Locations</span><span>Enterprise</span><span>Special promotions</span><span>Blog</span><span>Contact us</span><span>About us</span>
  </nav>
  <h1 class="hero-title abs">DESKHARBOR</h1>
  <p class="hero-sub abs">DeskHarbor is a new global coworking brand, growing fast and establishing stylish locations and</p>
  <svg class="hero-wave" viewBox="0 0 1200 40" preserveAspectRatio="none"><path d="M0 30 Q300 0 600 14 T1200 8 V40 H0Z" fill="#8cc7ea"/><path d="M0 38 Q300 10 600 22 T1200 18 V40 H0Z" fill="#fff"/></svg>
</header>

<!-- VALUES -->
<h2 class="section-title abs" style="top:622px">Values To Deliver</h2>
<div class="value abs" style="left:138px;top:694px">
  <div class="value-icon"><svg width="46" height="34" viewBox="0 0 46 34"><g fill="#8cc7ea"><circle cx="23" cy="8" r="6"/><circle cx="10" cy="11" r="5"/><circle cx="36" cy="11" r="5"/><path d="M13 30c0-7 4-12 10-12s10 5 10 12z"/><path d="M1 30c0-6 3-10 9-10 2 0 3 .3 4 1-2 2-3 5-3 9z"/><path d="M45 30c0-6-3-10-9-10-2 0-3 .3-4 1 2 2 3 5 3 9z"/></g></svg></div>
  <div><h3>Inspire collaboration &amp; Innovation</h3><p>Lorem ipsum dolor sit amet, consectetur elit, sed do eiusmod tempor ut labore et dolore magna adipisicing elit.</p></div>
</div>
<div class="value abs" style="left:685px;top:694px">
  <div class="value-icon"><svg width="36" height="36" viewBox="0 0 36 36"><g fill="#8cc7ea"><circle cx="27" cy="8" r="5"/><circle cx="9" cy="18" r="5"/><circle cx="27" cy="28" r="5"/></g><path d="M27 8L9 18l18 10" stroke="#8cc7ea" stroke-width="2.5" fill="none"/></svg></div>
  <div><h3>Idea sharing</h3><p>Lorem ipsum dolor sit amet, consectetur elit, sed do eiusmod tempor ut labore et dolore magna adipisicing elit.</p></div>
</div>
<div class="value abs" style="left:138px;top:830px">
  <div class="value-icon"><svg width="26" height="32" viewBox="0 0 26 32"><path d="M2 2h22v28l-11-8-11 8z" fill="#8cc7ea"/></svg></div>
  <div><h3>Be a part of an exclusive club</h3><p>Lorem ipsum dolor sit amet, consectetur elit, sed do eiusmod tempor ut labore et dolore magna adipisicing elit.</p></div>
</div>
<div class="value abs" style="left:685px;top:830px">
  <div class="value-icon"><svg width="36" height="36" viewBox="0 0 36 36"><g fill="#8cc7ea"><path d="M18 2l6 7h-12z"/><path d="M18 34l6-7h-12z"/><path d="M2 18l7-6v12z"/><path d="M34 18l-7-6v12z"/><circle cx="18" cy="18" r="6"/></g></svg></div>
  <div><h3>Realize your greatness</h3><p>Lorem ipsum dolor sit amet, consectetur elit, sed do eiusmod tempor ut labore et dolore magna adipisicing elit.</p></div>
</div>
<div class="btn abs" style="left:525px;top:965px;width:152px;height:39px;line-height:39px">VIEW MORE</div>

<!-- WHAT WE DO -->
<section class="what abs">
  <h2>What We Do?</h2>
  <p style="top:100px">DeskHarbor is focused on a stylish work environment that includes private offices, with shared lounges, meeting rooms and kitchens</p>
  <p style="top:172px">The project includes a complete website design, focused on delivering the company's values and messages, provide information to site visitors and to generate leads.</p>
  <div class="btn" style="position:absolute;left:98px;top:270px;width:118px;height:36px;line-height:36px">READ MORE</div>
</section>
<div class="what-photo abs" role="img" aria-label="Meeting room with long table, white chairs and wooden floor"></div>

<!-- TESTIMONIALS -->
<h2 class="section-title abs" style="top:1490px">Testimonials</h2>
<svg class="abs" style="left:82px;top:1694px" width="16" height="24" viewBox="0 0 16 24"><path d="M13 3L4 12l9 9" stroke="#222" stroke-width="4" fill="none"/></svg>
<svg class="abs" style="left:1100px;top:1694px" width="16" height="24" viewBox="0 0 16 24"><path d="M3 3l9 9-9 9" stroke="#222" stroke-width="4" fill="none"/></svg>

<div class="avatar abs" style="left:141px;top:1565px" role="img" aria-label="Portrait of a client"></div>
<div class="quote-badge abs" style="left:195px;top:1704px">”</div>
<p class="testimonial-text abs" style="left:77px;top:1758px">Lorem ipsum d, br adipelit, sed do eiusmodor is but  utisi lais ifbore ore magna aliqua</p>

<div class="avatar abs" style="left:522px;top:1565px" role="img" aria-label="Portrait of a client"></div>
<div class="quote-badge abs" style="left:576px;top:1704px">”</div>
<p class="testimonial-text abs" style="left:458px;top:1758px">Lorem ipsum d, br adipelit, sed do eiusmodor is but  utisi lais ifbore ore magna aliqua</p>

<div class="avatar abs" style="left:905px;top:1565px;background:linear-gradient(160deg,#e8a55b,#b86a2c)" role="img" aria-label="Portrait of a client"></div>
<div class="quote-badge abs" style="left:959px;top:1704px">”</div>
<p class="testimonial-text abs" style="left:841px;top:1758px">Lorem ipsum d, br adipelit, sed do eiusmodor is but  utisi lais ifbore ore magna aliqua</p>

<!-- MAP -->
<div class="map abs" role="img" aria-label="World map marking the cities with coworking locations"></div>
<div class="map-card abs"><h3>DESKHARBOR</h3><p>500 Office Locations 58 Cities</p></div>

<!-- NEWS -->
<h2 class="section-title abs" style="top:2410px">Latest News</h2>
<article class="news-card abs" style="left:98px">
  <div class="news-img" role="img" aria-label="Businessman signing a document" style="background:linear-gradient(135deg,#9aa7b0,#2f3a44)"></div>
  <p>Lorem ipsum dolor sit amet, consectetur adipiscing elit, sed do eiusmod tempor incididunt</p>
  <div class="news-meta"><span>💬 10</span><span>◷ March 5,2017</span></div>
</article>
<article class="news-card abs" style="left:456px">
  <div class="news-img" role="img" aria-label="Meeting table with white chairs" style="background:linear-gradient(180deg,#7f6d5c,#e9e9e9 60%,#c9c9c9)"></div>
  <p>Lorem ipsum dolor sit amet, consectetur adipiscing elit, sed do eiusmod tempor incididunt</p>
  <div class="news-meta"><span>💬 10</span><span>◷ March 5,2017</span></div>
</article>
<article class="news-card abs" style="left:826px">
  <div class="news-img" role="img" aria-label="Woman working on a laptop in a bright office" style="background:linear-gradient(135deg,#e6e6e6,#a5a5a5)"></div>
  <p>Lorem ipsum dolor sit amet, consectetur adipiscing elit, sed do eiusmod tempor incididunt</p>
  <div class="news-meta"><span>💬 10</span><span>◷ March 5,2017</span></div>
</article>

<!-- FOOTER -->
<footer class="footer abs">
  <svg class="footer-wave" viewBox="0 0 1200 36" preserveAspectRatio="none"><path d="M0 0H1200V20Q900 0 600 12T0 16Z" fill="#fff"/><path d="M0 16Q300 8 600 12T1200 20V24Q900 6 600 16T0 22Z" fill="#8cc7ea"/></svg>
  <div class="logo" style="position:absolute;left:98px;top:70px">DeskHarbor</div>
  <p class="blurb">Lorem ipsum dolor sit amet, consectetur adipiscing elit, sed do eiusmod tempor incididunt ut labore et dolore magna aliqua. Ut enim ad minim veniam, quis nostrud exercitation ullamco laboris nisi ut aliquip ex ea commodo consequat.</p>
  <div class="socials" aria-label="Social links"><span></span><span></span><span></span><span></span></div>
  <h4 style="position:absolute;left:525px;top:66px">QUICKLINKS</h4>
  <ul class="quicklinks"><li>Locations</li><li>Enterprise</li><li>Special promotions</li><li>Blog</li><li>Contact us</li><li>About us</li></ul>
  <h4 style="position:absolute;left:760px;top:66px">CONTACT FOR INFO</h4>
  <div class="field" style="top:130px">Name</div>
  <div class="field" style="top:170px">Email</div>
  <div class="field" style="top:210px">Subject</div>
  <div class="field" style="top:253px;height:68px">Message</div>
  <div class="btn" style="position:absolute;left:1029px;top:335px;width:72px;height:30px;line-height:30px;font-size:12px">SEND</div>
  <div class="footer-bottom">
    <span>©Copy Rights 2017.deskharbor-site.com.All Rights Reserved</span>
    <ul><li>Privacy policy</li><li>Terms &amp; conditions</li><li>Career</li></ul>
  </div>
</footer>

</body>
</html>
```